Fresh, modern, fun business card for pediatric dental practice

Need a business card for fresh, modern, fun pediatric dental practice

Clean look that matches our website's font and colors

We prefer the look of curved corners on business cards

Target Market(s)

parents (mothers) of young children, professionals, mid-high class

Industry/Entity Type

Dental

Contact Information for Business Card

Maplebrook Pediatric Dentistry
482 Quarry Lane
Suite 517
Alder Springs, PA 17008
717.555.0193
www.maplebrookkidsdental.example

Mei-Ran Tsai, DMD
Corinne Walbeck, DMD
(we are working on our email address, but we would like that on the card as well)

Font styles to use
Sans Serif

Requirements
Must have
• All info; we would also like to make cards for individual staff members
• colors from our website and color palatte, attatched
• use same font and design as website for branding
Nice to have
• clean, simple card that has a pop of color
• we would like to see a few designs with our tag line "where smiles get brighter"
• we are not sure if we want to have it on there or not
• we would like to see a few designs incorporating the ribbon graphic on our website where the word WELCOME is

```html
<!DOCTYPE html>
<html lang="en">
<head>
<meta charset="utf-8">
<title>Maplebrook Pediatric Dentistry – Business Card</title>
<link rel="stylesheet" href="https://fonts.googleapis.com/css2?family=Lato:wght@400;700;900&display=swap">
<style>
  :root {
    --bg: #1c1c1c;
    --card: #232323;
    --card-edge: #2b2b2b;
    --sun: #fbbf22;
    --berry: #d1359a;
    --ink: #f2f2f2;
  }
  * { margin: 0; padding: 0; box-sizing: border-box; }
  html, body { width: 1200px; height: 900px; overflow: hidden; }
  body {
    background: radial-gradient(ellipse at 60% 30%, #2e2e2e 0%, var(--bg) 70%);
    font-family: "Lato", sans-serif;
    position: relative;
  }
  .card {
    position: absolute;
    left: 220px;
    width: 760px;
    height: 420px;
    background: linear-gradient(135deg, var(--card) 0%, var(--card-edge) 100%);
    border-radius: 14px;
    overflow: hidden;
    box-shadow: 0 10px 30px rgba(0,0,0,.55);
  }
  .card::after {
    content: "";
    position: absolute;
    left: 0; right: 0; bottom: 0;
    height: 9px;
    background: var(--sun);
  }
  .card--front { top: 20px; }
  .card--back { top: 460px; }

  .wordmark {
    display: flex;
    flex-direction: column;
    align-items: center;
    color: var(--sun);
    font-weight: 700;
    line-height: 1;
  }
  .wordmark__dot {
    width: 46px; height: 46px;
    border-radius: 50%;
    background: var(--sun);
    margin-bottom: 16px;
  }
  .wordmark__name { font-size: 64px; letter-spacing: 4px; }
  .wordmark__sub { font-size: 27px; letter-spacing: 4px; margin-top: 8px; }

  .card--front .wordmark {
    position: absolute;
    left: 0; right: 0; top: 92px;
  }
  .front__url {
    position: absolute;
    left: 0; right: 0; top: 318px;
    text-align: center;
    color: var(--ink);
    font-size: 17px;
    letter-spacing: 2px;
  }
  .front__url span { color: var(--sun); }

  .card--back .wordmark {
    position: absolute;
    left: 30px; width: 340px; top: 112px;
  }
  .card--back .wordmark__name { font-size: 52px; letter-spacing: 3px; }
  .card--back .wordmark__sub { font-size: 22px; letter-spacing: 3px; }

  .divider {
    position: absolute;
    left: 400px; top: 70px;
    width: 3px; height: 250px;
    background: var(--berry);
  }
  .details {
    position: absolute;
    left: 436px; top: 88px;
    right: 20px;
    color: var(--ink);
  }
  .details__name {
    color: var(--sun);
    font-size: 25px;
    font-weight: 700;
    letter-spacing: 2px;
    text-transform: uppercase;
  }
  .details__title { font-size: 19px; margin-top: 2px; }
  .details__practice { color: var(--sun); font-size: 17px; margin-top: 18px; }
  .details__address { font-size: 17px; line-height: 1.3; font-style: normal; }
  .contact { list-style: none; margin-top: 16px; font-size: 17px; line-height: 1.55; }
  .contact li { display: flex; align-items: center; gap: 12px; white-space: nowrap; }
  .contact svg { width: 15px; height: 15px; fill: var(--sun); flex: none; }
</style>
</head>
<body>

<section class="card card--front" aria-label="Card front">
  <div class="wordmark">
    <span class="wordmark__dot"></span>
    <span class="wordmark__name">maplebrook</span>
    <span class="wordmark__sub">pediatric dentistry</span>
  </div>
  <p class="front__url">www.<span>maplebrookkidsdental</span>.example</p>
</section>

<section class="card card--back" aria-label="Card back">
  <div class="wordmark">
    <span class="wordmark__dot"></span>
    <span class="wordmark__name">maplebrook</span>
    <span class="wordmark__sub">pediatric dentistry</span>
  </div>
  <span class="divider"></span>
  <div class="details">
    <h1 class="details__name">Corinne Walbeck</h1>
    <p class="details__title">DMD</p>
    <p class="details__practice">Maplebrook Pediatric Dentistry</p>
    <address class="details__address">482 Quarry Lane<br>Suite 517 Alder Springs, PA 17008</address>
    <ul class="contact">
      <li>
        <svg viewBox="0 0 24 24" aria-hidden="true"><path d="M6.6 10.8a15.1 15.1 0 0 0 6.6 6.6l2.2-2.2c.3-.3.7-.4 1-.2 1.1.4 2.3.6 3.6.6.6 0 1 .4 1 1V20c0 .6-.4 1-1 1A17 17 0 0 1 3 4c0-.6.4-1 1-1h3.5c.6 0 1 .4 1 1 0 1.3.2 2.5.6 3.6.1.3 0 .7-.2 1z"/></svg>
        717.555.0193
      </li>
      <li>
        <svg viewBox="0 0 24 24" aria-hidden="true"><path d="M2 5h20v14H2zm2 2v.5l8 5 8-5V7l-8 5z"/></svg>
        info@maplebrookkidsdental.example
      </li>
      <li>
        <svg viewBox="0 0 24 24" aria-hidden="true"><path d="M12 2a10 10 0 1 0 0 20 10 10 0 0 0 0-20zm0 2c.9 1.2 1.6 2.6 2 4h-4c.4-1.4 1.1-2.8 2-4zM4.3 14a8 8 0 0 1 0-4h3.4a16 16 0 0 0 0 4zm.8 2h3c.3 1.3.8 2.5 1.5 3.6A8 8 0 0 1 5.1 16zm3-8h-3a8 8 0 0 1 4.5-3.6C8.9 5.5 8.4 6.7 8.1 8zM12 20c-.9-1.2-1.6-2.6-2-4h4c-.4 1.4-1.1 2.8-2 4zm2.3-6H9.7a14 14 0 0 1 0-4h4.6a14 14 0 0 1 0 4zm.1 5.6c.7-1.1 1.2-2.3 1.5-3.6h3a8 8 0 0 1-4.5 3.6zM16.3 14a16 16 0 0 0 0-4h3.4a8 8 0 0 1 0 4zm-.4-6c-.3-1.3-.8-2.5-1.5-3.6A8 8 0 0 1 18.9 8z"/></svg>
        www.maplebrookkidsdental.example
      </li>
    </ul>
  </div>
</section>

</body>
</html>
```